Corporate Business Card

Very professional, Modern, Not to busy, include phone address email, website
(253) 617-4930, 18761 52nd Avenue S, Kent, WA 98047, martin@plumlinegroup.com, varkoworks.com

Target Market(s)

Manufacturing

Industry/Entity Type

Aero, machining, manufacturing, Off road racing

Contact Information for Business Card

Phone, address email, website

```html
<!DOCTYPE html>
<html lang="en">
<head>
<meta charset="utf-8">
<title>Varko Works Business Card</title>
<link href="https://fonts.googleapis.com/css2?family=Roboto:wght@400;700;900&display=swap" rel="stylesheet">
<style>
  :root {
    --page: #e6e6e6;
    --paper: #f6f6f7;
    --navy: #1b3a73;
    --navy-deep: #14306a;
    --navy-top: #1f4176;
    --red: #c9252c;
    --ink: #3a3a3a;
    --muted: #7c7c7c;
    --rule: #c8c8c8;
    --emboss: #2a4f88;
  }
  * { margin: 0; padding: 0; box-sizing: border-box; }
  html, body { width: 1200px; height: 1200px; overflow: hidden; }
  body {
    background: var(--page);
    font-family: "Roboto", Arial, sans-serif;
    position: relative;
  }
  .card {
    position: absolute;
    left: 262px;
    width: 686px;
    height: 392px;
    overflow: hidden;
  }
  .card-front { top: 165px; background: var(--paper); }
  .card-back {
    top: 653px;
    background: linear-gradient(180deg, var(--navy-top) 0%, var(--navy-deep) 100%);
  }

  .brand {
    position: absolute;
    left: 0;
    width: 352px;
    top: 174px;
    text-align: center;
    color: var(--navy);
    font-weight: 900;
    font-size: 40px;
    letter-spacing: 1px;
    line-height: 1;
  }

  .divider {
    position: absolute;
    left: 352px;
    top: 84px;
    width: 1px;
    height: 221px;
    background: var(--rule);
  }

  .contact {
    position: absolute;
    left: 368px;
    top: 106px;
    color: var(--ink);
  }
  .contact-name {
    color: var(--navy);
    font-weight: 700;
    font-size: 26px;
    line-height: 1;
  }
  .contact-title {
    color: var(--muted);
    font-size: 15px;
    margin-top: 4px;
  }
  .contact-address {
    font-size: 16px;
    line-height: 21px;
    margin-top: 13px;
  }
  .contact-lines { list-style: none; margin-top: 13px; }
  .contact-lines li {
    font-size: 16px;
    line-height: 20.5px;
    display: flex;
    align-items: center;
    gap: 10px;
  }
  .contact-lines svg { width: 15px; height: 15px; flex: none; }

  .band {
    position: absolute;
    left: 0;
    bottom: 0;
    width: 686px;
    height: 16px;
  }

  .brand-back {
    position: absolute;
    left: 0;
    right: 0;
    top: 160px;
    text-align: center;
    color: var(--emboss);
    font-weight: 900;
    font-size: 68px;
    letter-spacing: 2px;
    line-height: 1;
  }
</style>
</head>
<body>
  <section class="card card-front">
    <div class="brand">VARKO WORKS</div>
    <div class="divider"></div>
    <div class="contact">
      <h1 class="contact-name">DANIEL MORROW</h1>
      <p class="contact-title">Managing Director</p>
      <p class="contact-address">18761 52nd Avenue S<br>Kent, WA 98047</p>
      <ul class="contact-lines">
        <li>
          <svg viewBox="0 0 16 16" aria-hidden="true"><path fill="#c9252c" d="M3.6 1.2l2.2 2.9-1.3 1.6c.9 2 2.6 3.7 4.6 4.7l1.6-1.3 2.9 2.2-1.2 2.6C7.5 14 2 8.5 1 3.9z"/></svg>
          (253) 617-4930
        </li>
        <li>
          <svg viewBox="0 0 16 16" aria-hidden="true"><rect x="1" y="4" width="14" height="9" fill="#c9252c"/><path d="M1.5 4.5L8 9.5l6.5-5" stroke="#f6f6f7" stroke-width="1.2" fill="none"/></svg>
          martin@plumlinegroup.com
        </li>
        <li>
          <svg viewBox="0 0 16 16" aria-hidden="true"><circle cx="8" cy="8" r="6.5" fill="#c9252c"/><path d="M5 5.5c1 .2 1.5 1 1.2 2s.8 1.5 1.6 1.3M9.5 3.5c-.3 1 .5 1.6 1.5 1.5M9 12c.2-1 1-1.6 2-1.8" stroke="#f6f6f7" stroke-width="1.1" fill="none"/></svg>
          varkoworks.com
        </li>
      </ul>
    </div>
    <svg class="band" viewBox="0 0 686 16" preserveAspectRatio="none" aria-hidden="true">
      <polygon points="0,0 394,0 382,16 0,16" fill="#1b3a73"/>
      <polygon points="399,0 686,0 686,16 387,16" fill="#c9252c"/>
    </svg>
  </section>

  <section class="card card-back">
    <div class="brand-back">VARKO WORKS</div>
  </section>
</body>
</html>
```